Money Mindset Podcast needs fun, creative cover art

Launching a new podcast called 'Turning Your Thoughts Toward Savings' - aimed at an audience 30-50 who are interested in the practicalities of managing their money but also the more mental and emotional aspects.
Looking for something not too serious, warm and friendly.

Must be easy to read on phone screens
3000 x 3000 in size
Avoid currency symbols $, £ etc, as may have an international audience

Target Market(s)

Podcast listeners age 30-50 starting in the UK but then worldwide. Probably 60:40 female bias

Industry/Entity Type

Life Coaching

Font styles to use
Serif
Sans Serif

Colors
cadf82
fee18a
acd037
85cae6
eea4c8
f59195
85acd3

Requirements
Must have
• Simple, clear design. Easy to read on variety of devices. 3000 x 3000
Appeal to those with a spiritual or emotional interests
Nice to have
• Stand out among other money related podcasts
Maybe play around with clouds, lightbulbs and clearing skies
Should not have
• Currency symbols such as $ or £
Be too corporate or bank like
Stock images

```html
<!DOCTYPE html>
<html lang="en">
<head>
<meta charset="utf-8">
<title>Turning Your Thoughts Toward Savings – Podcast Cover</title>
<link rel="stylesheet" href="https://fonts.googleapis.com/css2?family=Bebas+Neue&display=swap">
<style>
  :root {
    --night-deep: #1d1838;
    --night-plum: #2e2452;
    --night-violet: #3b2e62;
    --glow-sun: #fee18a;
    --glow-coral: #f59195;
    --glow-rose: #eea4c8;
    --haze-blue: #85acd3;
    --title-white: #ffffff;
    --title-butter: #fee18a;
    --title-rose: #eea4c8;
    --title-sky: #85cae6;
  }
  html, body {
    margin: 0;
    padding: 0;
    width: 1200px;
    height: 1200px;
    overflow: hidden;
    background: var(--night-deep);
  }
  .cover {
    position: relative;
    width: 1200px;
    height: 1200px;
    overflow: hidden;
    background: var(--night-deep);
  }
  .cover__backdrop {
    position: absolute;
    inset: 0;
    background:
      radial-gradient(circle at 925px 600px, #fff8dc 0, rgba(254,225,138,0.95) 40px, rgba(245,145,149,0.55) 150px, rgba(238,164,200,0.28) 320px, rgba(133,172,211,0.12) 460px, rgba(0,0,0,0) 560px),
      linear-gradient(180deg, var(--night-deep) 0%, var(--night-plum) 45%, var(--night-violet) 75%, var(--night-deep) 100%);
  }
  .cover__title {
    position: absolute;
    inset: 0;
    width: 1200px;
    height: 1200px;
  }
  .title-line {
    font-family: "Bebas Neue", "Oswald", sans-serif;
    fill: var(--title-white);
  }
  .title-line--sub { fill: var(--title-butter); }
  .title-line--bridge { fill: var(--title-rose); }
  .title-line--hero { fill: var(--title-sky); }
</style>
</head>
<body>
  <main class="cover">
    <div class="cover__backdrop" role="img" aria-label="Warm glowing light bulb hanging in a soft twilight haze"></div>
    <svg class="cover__title" viewBox="0 0 1200 1200" aria-label="Turning Your Thoughts Toward Savings">
      <text class="title-line title-line--lead" x="60" y="300" font-size="366" textLength="1090" lengthAdjust="spacingAndGlyphs">TURNING</text>
      <text class="title-line title-line--sub" x="40" y="520" font-size="214" textLength="740" lengthAdjust="spacingAndGlyphs">YOUR THOUGHTS</text>
      <text class="title-line title-line--bridge" x="40" y="730" font-size="228" textLength="460" lengthAdjust="spacingAndGlyphs">TOWARD</text>
      <text class="title-line title-line--hero" x="40" y="1170" font-size="557" textLength="1140" lengthAdjust="spacingAndGlyphs">SAVINGS</text>
    </svg>
  </main>
</body>
</html>
```